New Bicycle shop business card

Hi!
I'm looking for a business card for my new proffesional bike mechanics shop. This shop is only for fixing broken bikes and not selling bikes.
Peferbly a modern and sleek and modern design.
Colors: black, grey, red, white
Information:
Name: Rijwielwerkplaats Vanhoutte
Shop owner: Bart Vanhoutte & Marieke Segers
Website: www.rijwielwerkplaats-vanhoutte.be
Email: info@rijwielwerkplaats-vanhoutte.be
Phone number: +32471902368
Street adres: Kerkweg 46
9940 Bellebeke
Slogan/shop information: Herstellingen van alle merken.
Logo: see files.
Target Market(s)
People who seek a mechanic to fix or upgrade their bikes.
Contact Information for Business Card
Information:
Website: info@rijwielwerkplaats-vanhoutte.be
9940 Bellebeke
Logo: see files.

```html
<!DOCTYPE html>
<html lang="nl">
<head>
<meta charset="utf-8">
<title>Rijwielwerkplaats Vanhoutte – Visitekaartje</title>
<link rel="stylesheet" href="https://fonts.googleapis.com/css2?family=Lato:wght@400;700;900&display=swap">
<style>
  :root {
    --backdrop: #2b2724;
    --card: #0d0d0d;
    --card-edge: #1a1a1a;
    --red: #e3293b;
    --white: #f2f2f2;
    --silver: #c9c9c9;
    --grey: #9a9a9a;
    --divider: #2e2e2e;
  }
  * { margin: 0; padding: 0; box-sizing: border-box; }
  html, body {
    width: 1200px; height: 844px; overflow: hidden;
    background: var(--backdrop);
    font-family: "Lato", Arial, sans-serif;
  }
  .stage {
    width: 1200px; height: 844px;
    display: flex; align-items: center; justify-content: center; gap: 40px;
  }
  .card {
    width: 540px; height: 310px;
    background: var(--card);
    border: 1px solid var(--card-edge);
    position: relative;
  }
  /* Front: contact side */
  .card--contact { display: flex; }
  .brand-block {
    width: 250px; display: flex; align-items: center; justify-content: center; gap: 12px;
    padding: 0 20px;
  }
  .brand-block__square { width: 18px; height: 18px; background: var(--red); flex: none; }
  .brand-block__name {
    color: var(--white); font-weight: 900; font-size: 19px; line-height: 1.15;
    text-transform: uppercase; letter-spacing: .5px;
  }
  .card__divider { width: 1px; margin: 50px 0; background: var(--divider); }
  .contact {
    padding: 64px 0 0 26px; color: var(--grey); font-size: 14px; line-height: 1.35;
  }
  .contact__names { color: var(--red); font-weight: 700; text-transform: uppercase; font-size: 13.5px; }
  .contact__role { margin-bottom: 2px; }
  .contact__line { display: flex; align-items: center; gap: 7px; white-space: nowrap; }
  .contact__line svg { width: 10px; height: 10px; flex: none; fill: var(--red); }
  .contact__address { margin-top: 12px; }
  /* Back: brand side */
  .card--brand {
    display: flex; flex-direction: column; align-items: center; justify-content: center; gap: 14px;
  }
  .brand-mark { display: flex; align-items: center; gap: 14px; }
  .brand-mark__square { width: 22px; height: 22px; background: var(--silver); }
  .brand-mark__name {
    color: var(--silver); font-weight: 900; font-size: 24px; letter-spacing: 2px;
    text-transform: uppercase; line-height: 1.15; text-align: center;
  }
  .tagline { color: var(--white); font-size: 12px; font-weight: 700; letter-spacing: .4px; text-transform: uppercase; }
</style>
</head>
<body>
<main class="stage">
  <section class="card card--contact">
    <div class="brand-block">
      <span class="brand-block__square"></span>
      <span class="brand-block__name">Rijwielwerkplaats<br>Vanhoutte</span>
    </div>
    <div class="card__divider"></div>
    <div class="contact">
      <p class="contact__names">Bart Vanhoutte &amp; Marieke Segers</p>
      <p class="contact__role">Owner</p>
      <p class="contact__line">
        <svg viewBox="0 0 10 10"><path d="M2 0h2l1 3-1.5 1a6 6 0 0 0 2.5 2.5L7 5l3 1v2c0 1-1 2-2 2A8 8 0 0 1 0 2c0-1 1-2 2-2z"/></svg>
        +32471902368</p>
      <p class="contact__line">
        <svg viewBox="0 0 10 10"><path d="M0 2h10v1L5 6 0 3z M0 4l5 3 5-3v4H0z"/></svg>
        info@rijwielwerkplaats-vanhoutte.be</p>
      <p class="contact__line">
        <svg viewBox="0 0 10 10"><circle cx="5" cy="5" r="5"/></svg>
        www.rijwielwerkplaats-vanhoutte.be</p>
      <p class="contact__address">Kerkweg 46<br>9940 Bellebeke</p>
    </div>
  </section>

  <section class="card card--brand">
    <div class="brand-mark">
      <span class="brand-mark__square"></span>
      <span class="brand-mark__name">Rijwielwerkplaats<br>Vanhoutte</span>
    </div>
    <p class="tagline">Herstellingen van alle merken</p>
  </section>
</main>
</body>
</html>
```